Letterhead Design for Law Firm

**Edit: I have added the photo of a bottom that I like.

------
We are looking for a re-design of our new letterhead. The letterhead is for a law firm and will be used for digital and traditionally printed correspondence.

Here are some suggestions:

- Please use colours are #8ec900 and simple black.
- Please do not use any type of "waves" at the bottom of the page. This is not in style at all.
- Please stay modern yet conservative.
- Please use font Segoe UI Light or similar if you can
- Avoid clipart or illustrations.
- Utilize ample white space in the layout so the design looks clean and information is easy to read at a glance. Don't overcrowd the letterhead.
- Make sure the letterhead design is consistent with our brand identity (see corvelith.ca)
-Please, no black headers or footers.

I am attaching my current letterhead and signature for your convenience.

Remember, the letterhead is an extension of our professional identity. We are a successful firm and trial lawyers who correspond with insurers, judges, lawyers, courts, clients, etc. Make it new, modern, attractive, yet powerful and conservative.

It needs to be easily printable. I would like the bleed removed in print so the black bar the bottom crosses the page (but the text is not near the edges)
Updates

Low design quality

Target Market(s)

Clients, Government Offices, Judiciary, Lawyers, Insurance Companies, Colleagues.

Industry/Entity Type

Law

Other font styles liked:
• Segoe UI LIght, Calibri Light,

Colors
00AB8E
00BBA5
67D7C9
C6EFE9
E9F9F6

Requirements
Must have
• Everything that is on the letterhead now.
Nice to have
• Cutting Edge design, yet conservative.
Should not have
• law firm cliche design, images,

```html
<!DOCTYPE html>
<html lang="en">
<head>
<meta charset="utf-8">
<title>Hartwell Letterhead</title>
<link href="https://fonts.googleapis.com/css2?family=Open+Sans:wght@300;400;600;700&display=swap" rel="stylesheet">
<style>
  :root {
    --green: #8ac11f;
    --green-soft: rgba(138,193,31,0);
    --black: #111111;
    --ink: #2a2a2a;
    --muted: #555555;
    --paper: #ffffff;
    --backdrop: #e4e4e4;
  }
  * { margin: 0; padding: 0; box-sizing: border-box; }
  html, body { width: 1200px; height: 874px; overflow: hidden; }
  body {
    background: var(--backdrop);
    font-family: "Open Sans", "Segoe UI", sans-serif;
    color: var(--ink);
    display: flex; align-items: center; justify-content: center;
  }
  .letterhead {
    position: relative;
    width: 600px; height: 776px;
    background: var(--paper);
    box-shadow: 0 4px 18px rgba(0,0,0,.12);
    overflow: hidden;
    font-size: 10px; line-height: 1.45;
  }
  .corner-band {
    position: absolute; right: 0; bottom: 0;
    width: 330px; height: 230px;
    background: radial-gradient(ellipse at 100% 100%, var(--green) 0%, var(--green) 45%, var(--green-soft) 75%);
  }
  .firm-name {
    position: absolute; left: 46px; top: 58px;
    font-weight: 600; color: var(--black);
  }
  .firm-name .name { display: block; font-size: 36px; letter-spacing: 2px; line-height: 1; }
  .firm-name .tagline { display: block; font-size: 10.5px; letter-spacing: 2.4px; text-transform: uppercase; margin-top: 6px; }
  .contact-panel {
    position: absolute; left: 392px; top: 48px;
    border-left: 1.5px solid var(--green);
    padding: 2px 0 4px 10px;
    font-size: 7.5px; line-height: 1.45; color: var(--ink);
    font-style: normal;
  }
  .contact-panel .web b { color: var(--green); font-weight: 400; }
  .contact-panel strong { font-weight: 700; }
  .contact-panel .practice { margin-top: 7px; }
  .letter-body { position: absolute; left: 46px; top: 150px; right: 46px; }
  .letter-body p { margin-bottom: 9px; }
  .strong { font-weight: 700; }
  .recipient { margin: 14px 0 12px; }
  .re-line {
    display: flex; gap: 120px; margin-top: 14px;
    padding-bottom: 8px; border-bottom: 1px solid var(--muted);
  }
  .re-line .subject { font-weight: 700; line-height: 1.5; }
  .sign-off { position: absolute; left: 300px; top: 470px; font-size: 10px; line-height: 1.45; }
  .sign-off .firm { text-transform: uppercase; }
  .signature {
    display: block; width: 150px; height: 36px; margin: 6px 0 4px;
    background: linear-gradient(90deg, rgba(17,17,17,.12), rgba(17,17,17,.04));
    border-radius: 3px;
  }
  .sign-off .small { font-size: 9px; }
</style>
</head>
<body>
  <main class="letterhead">
    <div class="corner-band" role="img" aria-label="Decorative green and black corner band"></div>

    <div class="firm-name">
      <span class="name">HARTWELL</span>
      <span class="tagline">Personal Injury Lawyers</span>
    </div>

    <address class="contact-panel">
      <div class="web">www.<b>CORVELITH</b>.ca</div>
      <div>40 Elm Street W., Suite 900</div>
      <div>Hamilton, ON &nbsp;L8R 2K6</div>
      <div><strong>T:</strong> 555-210-4400</div>
      <div><strong>F:</strong> 555-210-4401</div>
      <div><strong>File Clerk:</strong> Nora Whitfield</div>
      <div><strong>Email:</strong> nora@corvelith.ca</div>
      <div class="practice"><strong>Practice Restricted</strong></div>
      <div>Serious Personal Injury</div>
      <div>Wrongful Death Litigation</div>
      <div>Long-Term Disability Litigation</div>
      <div>Wrongful Dismissal Litigation</div>
      <div>Employee Terminations</div>
    </address>

    <section class="letter-body">
      <p class="strong">Without Prejudice</p>
      <p>March 13, 2024</p>
      <p class="strong">By Email</p>
      <div class="recipient">
        Brightmoor Insurance Company<br>
        Claims Litigation Department<br>
        220 Ridgeview Road South<br>
        P.O. Box 3100<br>
        Elmdale, ON &nbsp;&nbsp;N3K 7T2
      </div>
      <p>Attention: &nbsp;Ms. Dana Colby</p>
      <p>Ms. Colby:</p>
      <div class="re-line">
        <span class="strong">Re:</span>
        <span class="subject">Pardell v. Osgood et al.<br>DOL: &nbsp;September 12, 2019<br>Pre-Mediation Settlement Proposal – March 13<sup>th</sup>, 2024</span>
      </div>
    </section>

    <div class="sign-off">
      <div>Yours very truly,</div>
      <div class="firm">Hartwell Personal Injury Lawyers</div>
      <span class="signature" role="img" aria-label="Handwritten signature of Evan R. Hartwell"></span>
      <div>Evan R. Hartwell</div>
      <div class="small">Hartwell Law Professional Corporation</div>
      <div class="small">/nw</div>
      <div class="small">Encl.</div>
    </div>
  </main>
</body>
</html>
```